Letter and Envelope Design For Harborline Realty

Please design a letter and an envelope incorporating our logo (See Attached). We are also launched a business card contest. Since we want them to match, please feel free to submit a design for both the business card and also the letter design and envelope.

Requirements
Must have
• The envelope, the letter and the business cards must match somehow connecting the designs. We want them to have something that holds them together besides the logo.

```html
<!DOCTYPE html>
<html lang="en">
<head>
<meta charset="utf-8">
<title>Harborline Realty – Letterhead and Envelope</title>
<link rel="stylesheet" href="https://fonts.googleapis.com/css2?family=Montserrat:wght@600&family=Source+Sans+3:wght@400;700&display=swap">
<style>
  :root{
    --navy:#0c1c8f;
    --slate:#58595b;
    --paper:#fafafa;
    --ink:#3a3a3a;
    --backdrop:#e4e4e4;
  }
  *{box-sizing:border-box;margin:0;padding:0}
  html,body{width:1200px;height:825px;overflow:hidden;background:var(--backdrop)}
  .canvas{position:relative;width:1200px;height:825px}
  .sheet{position:absolute;background:var(--paper);box-shadow:0 1px 4px rgba(0,0,0,.15);overflow:hidden}
  .letter{left:164px;top:173px;width:460px;height:652px}
  .envelope-front{left:666px;top:174px;width:530px;height:230px}
  .envelope-back{left:666px;top:430px;width:530px;height:231px}

  .brand{position:absolute;left:0;right:0;text-align:center}
  .brand-dot{display:block;margin:0 auto;width:42px;height:42px;border:2px solid var(--navy);border-radius:50%}
  .brand-name{display:block;margin-top:6px;font-family:"Montserrat",sans-serif;font-weight:600;font-size:12px;letter-spacing:1.6px;color:var(--navy);text-transform:uppercase}
  .letter .brand{top:14px}
  .envelope-front .brand{top:13px}

  .letter-body{position:absolute;left:30px;top:150px;width:401px;font-family:"Source Sans 3",sans-serif;color:var(--ink)}
  .salutation{font-weight:700;font-size:11px;color:#222;margin-bottom:12px}
  .letter-body p{font-size:9.6px;line-height:12px;text-align:justify;margin-bottom:12px}
  .signature{position:absolute;left:30px;top:381px;width:88px;height:44px;background:#ececec;border-radius:3px}

  .footer-wave{position:absolute;left:0;bottom:0;width:100%}
  .letter .footer-wave{height:93px}
  .envelope-front .footer-wave{height:96px}
  .footer-wave svg{display:block;width:100%;height:100%}

  .contact{position:absolute;font-family:"Source Sans 3",sans-serif;color:#fff;font-size:6.8px;line-height:10px}
  .contact strong{font-weight:700}
  .contact-address{left:35px;bottom:5px}
  .contact-lines{right:35px;bottom:5px;text-align:right}
  .envelope-front .contact-address{left:39px;bottom:8px}
  .envelope-front .contact-lines{right:42px;bottom:10px}
  .icon{display:inline-block;width:7px;margin-left:3px;text-align:center}

  .flap{position:absolute;left:0;top:0;width:100%;height:53px;background:var(--slate);border-radius:0 0 60px 60px / 0 0 53px 53px}
</style>
</head>
<body>
<div class="canvas">

  <section class="sheet letter">
    <div class="brand">
      <span class="brand-dot"></span>
      <span class="brand-name">Harborline Realty</span>
    </div>

    <div class="letter-body">
      <div class="salutation">Dear Mr. Avery,</div>
      <p>Lorem Ipsum is simply dummy text of the printing and typesetting industry. Lorem Ipsum has been the industry's standard dummy text ever since the 1500s, when an unknown printer took a galley of type and scrambled it to make a type specimen book. It has survived not only five centuries, but also the leap into electronic typesetting, remaining essentially unchanged.</p>
      <p>The standard chunk of Lorem Ipsum used since the 1500s is reproduced below for those interested. Sections 1.10.32 and 1.10.33 from "de Finibus Bonorum et Malorum" by Aurelio Brann are also reproduced in their exact original form, accompanied by English versions from the 1914 translation by L. Whitcombe</p>
      <p>Lorem Ipsum is simply dummy text of the printing and typesetting industry. Lorem Ipsum has been the industry's standard dummy text ever since the 1500s, when an unknown printer took a galley of type and scrambled it to make a type specimen book. It has survived not only five centuries, but also the leap into electronic typesetting, remaining essentially unchanged. It was popularised in the</p>
    </div>

    <div class="signature" role="img" aria-label="Handwritten signature of the sender"></div>

    <div class="footer-wave">
      <svg viewBox="0 0 460 93" preserveAspectRatio="none" aria-hidden="true">
        <path d="M0,4 Q230,92 460,14 L460,32 Q230,80 0,20 Z" fill="var(--slate)"/>
        <path d="M0,34 Q230,98 460,36 L460,93 L0,93 Z" fill="var(--navy)"/>
        <path d="M95,52 Q300,66 460,38 L460,43 Q300,72 95,52 Z" fill="var(--slate)"/>
      </svg>
      <div class="contact contact-address">
        <strong>Harborline Realty</strong><br>
        Po. box 201, Street Name,<br>
        City Name, Zip Code - 00000
      </div>
      <div class="contact contact-lines">
        555-014-2290<span class="icon">☎</span><br>
        info@harborline.com<span class="icon">✉</span><br>
        info@harborline.com<span class="icon">⊕</span>
      </div>
    </div>
  </section>

  <section class="sheet envelope-front">
    <div class="brand">
      <span class="brand-dot"></span>
      <span class="brand-name">Harborline Realty</span>
    </div>
    <div class="footer-wave">
      <svg viewBox="0 0 530 96" preserveAspectRatio="none" aria-hidden="true">
        <path d="M0,2 Q265,96 530,12 L530,30 Q265,84 0,26 Z" fill="var(--slate)"/>
        <path d="M0,36 Q265,104 530,34 L530,96 L0,96 Z" fill="var(--navy)"/>
        <path d="M90,56 Q330,70 530,36 L530,41 Q330,76 90,56 Z" fill="var(--slate)"/>
      </svg>
      <div class="contact contact-address">
        <strong>Harborline Realty</strong><br>
        Po. box 201, Street Name,<br>
        City Name, Zip Code - 00000
      </div>
      <div class="contact contact-lines">
        555-014-2290<span class="icon">☎</span><br>
        info@harborline.com<span class="icon">✉</span><br>
        info@harborline.com<span class="icon">⊕</span>
      </div>
    </div>
  </section>

  <section class="sheet envelope-back">
    <div class="flap"></div>
  </section>

</div>
</body>
</html>
```